Pebblebrook Plots - Online-only garden installation company

Online-only garden installation company. Our demographic is middle aged / suburban women, and we anticipate Facebook driving traffic to this website, as well as referrals from garden centers. The website must be very simple in design and function.

All orders will be placed through the website, including size of garden (3 options), location in yard, payment, and scheduling of installation date.

The website should employ a 3 step process:

Step 1: Select garden size. Either an 4' X 4', 8' X 4', or 12' X 4'.

Step 2: Select a location. We would like to use an online map to look up a US address, then "drag and drop" one of the garden sizes from step 1 to the location the customer would like us to install the garden at their home.

Step 3: Pick an installation date and pay. Using an online calendar the customer will pick a date, and then pay for the installation via credit card.

The website will be linked to an email account, PebblebrookPlots@mailvale.com to inform us of orders placed.

Target Market(s)

Our demographic is middle aged / suburban women, and we anticipate Facebook driving traffic to this website, as well as referrals from garden centers.

Industry/Entity Type

Coding

Number of Pages Required

Requirements
Must have
• Scheduling and payment options.

```html
<!DOCTYPE html>
<html lang="en">
<head>
<meta charset="utf-8">
<title>Pebblebrook Plots</title>
<link rel="stylesheet" href="https://fonts.googleapis.com/css2?family=Lora:ital,wght@0,400;0,700;1,400;1,700&family=Open+Sans:ital,wght@0,400;0,600;0,700;1,700&display=swap">
<style>
:root{
  --orange:#e05a2b;
  --orange-dark:#c94c20;
  --green:#3a7d2c;
  --green-dark:#2c6322;
  --ink:#2b2b2b;
  --muted:#6c6c6c;
  --line:#dcdcdc;
  --cream:#f8f3ef;
  --white:#ffffff;
}
*{box-sizing:border-box;margin:0;padding:0}
html,body{width:1200px;height:2695px;overflow:hidden}
body{position:relative;font-family:"Open Sans",Arial,sans-serif;color:var(--ink);background:var(--white)}
.abs{position:absolute}
h2{font-family:"Lora",Georgia,serif;font-weight:700;font-size:30px;color:var(--ink)}
p{font-size:12.5px;line-height:22px;color:var(--muted)}

/* header */
.site-header{left:0;top:0;width:1200px;height:90px;background:var(--white)}
.topbar{right:40px;top:12px;display:flex;gap:26px;align-items:center;font-size:15px;font-weight:600}
.topbar span{display:flex;align-items:center;gap:12px}
.ico-ring{width:34px;height:34px;border-radius:50%;border:2px solid var(--orange);display:flex;align-items:center;justify-content:center}
.ico-ring.green{border-color:var(--green)}
.main-nav{right:40px;top:58px;display:flex;gap:32px;font-size:15px;font-weight:600;align-items:center}
.logo-disc{left:72px;top:8px;width:216px;height:216px;border-radius:50%;background:var(--white);z-index:3;display:flex;flex-direction:column;align-items:center;justify-content:center;gap:4px}
.logo-mark{width:22px;height:22px;border-radius:50%;background:var(--orange)}
.logo-name{font-family:"Lora",Georgia,serif;font-weight:700;font-size:24px;color:var(--green-dark);text-align:center;line-height:28px}

/* hero */
.hero{left:0;top:90px;width:1200px;height:446px;background:linear-gradient(180deg,#6f7f5c 0%,#5f8a3e 40%,#4f8a2c 70%,#3f7a22 100%)}
.hero-title{left:99px;top:252px;font-family:"Lora",Georgia,serif;font-weight:700;font-size:46px;color:var(--white);letter-spacing:1px}
.hero-tag{left:99px;top:316px;font-family:"Open Sans",Arial,sans-serif;font-style:italic;font-weight:700;font-size:27px;color:var(--white)}
.btn-ghost{left:99px;top:372px;width:170px;height:44px;border:2px solid var(--white);border-radius:22px;color:var(--white);font-size:14px;font-weight:700;display:flex;align-items:center;justify-content:center}
.hero-arrow{top:300px;color:rgba(255,255,255,.8);font-size:32px}

.order-panel{left:711px;top:111px;width:388px;height:406px;background:var(--white);border-radius:6px;overflow:hidden;box-shadow:0 2px 8px rgba(0,0,0,.2)}
.order-head{height:50px;background:var(--orange);color:var(--white);font-family:"Lora",Georgia,serif;font-weight:700;font-size:23px;display:flex;align-items:center;justify-content:center}
.order-body{padding:14px 18px;font-size:12px}
.field-label{margin-top:10px;margin-bottom:8px;color:var(--ink)}
.radios{display:flex;gap:26px;font-size:11px;color:var(--muted)}
.radios span{display:flex;gap:7px;align-items:center}
.dot{width:11px;height:11px;border-radius:50%;border:1.5px solid #777}
.dot.on{background:var(--orange);border-color:var(--orange)}
.select{height:32px;border:1px solid var(--line);border-radius:2px;display:flex;align-items:center;justify-content:space-between;padding-left:14px;font-size:11px;color:#999}
.select i{width:30px;height:30px;border-left:1px solid var(--line);display:flex;align-items:center;justify-content:center;font-style:normal}
.cards{display:flex;gap:8px}
.card{width:56px;height:34px;border:1px solid var(--line);border-radius:3px;background:#f3f3f3;display:flex;align-items:center;justify-content:center;font-size:11px;font-weight:700;color:#555}
.btn-green{background:var(--green);color:var(--white);font-weight:700;display:flex;align-items:center;justify-content:center;border-radius:22px}

/* how it works */
.section-title{width:1200px;text-align:center}
.intro{left:250px;width:700px;text-align:center}
.step{width:330px;text-align:center}
.step-ring{width:172px;height:172px;border-radius:50%;border:2px solid var(--orange);margin:0 auto;display:flex;align-items:center;justify-content:center}
.step-ring.green{border-color:var(--green)}
.step-core{width:156px;height:156px;border-radius:50%;border:5px solid var(--orange);display:flex;align-items:center;justify-content:center}
.step-ring.green .step-core{border-color:var(--green)}
.step h3{font-family:"Lora",Georgia,serif;font-weight:700;font-size:21px;margin-top:34px;margin-bottom:14px}
.step p{font-size:11.5px;line-height:22px}
.connector{top:803px;height:2px;background:var(--line);width:170px}

/* what we do */
.what{left:0;top:1099px;width:1200px;height:392px;background:var(--cream)}
.video{left:609px;top:1149px;width:488px;height:282px;background:linear-gradient(160deg,#6b8f3a 0%,#4a3a26 55%,#2e2318 100%);border:4px solid var(--white);box-shadow:0 0 0 1px var(--line)}
.play{left:214px;top:111px;width:60px;height:60px;border-radius:50%;background:rgba(0,0,0,.75);display:flex;align-items:center;justify-content:center}
.btn-outline{border:2px solid var(--green);color:var(--green-dark);border-radius:18px;font-weight:700;font-size:12px;display:flex;align-items:center;justify-content:center}

/* services */
.services{left:0;top:1491px;width:1200px;height:517px;background:var(--orange)}
.services h2{color:var(--white)}
.service-card{top:1598px;width:310px;height:338px;background:var(--white);text-align:center}
.service-img{height:180px}
.service-card h3{font-family:"Lora",Georgia,serif;font-weight:700;font-size:20px;margin:20px 0 10px}
.service-card p{font-size:11.5px;line-height:20px;padding:0 22px;color:var(--muted)}
.service-card .btn-green{position:absolute;left:86px;bottom:-12px;width:138px;height:34px;font-size:12px}

/* gallery */
.gallery-img{top:2125px;width:242px;height:183px;border:4px solid var(--white);box-shadow:0 0 0 1px var(--line)}
.g-arrow{top:2195px;font-size:34px;color:#aaa}

/* footer */
.footer-rule{left:0;top:2367px;width:1200px;height:4px;background:var(--green)}
.footer-col h4{font-family:"Lora",Georgia,serif;font-weight:700;font-size:19px;margin-bottom:22px}
.footer-col li{list-style:none;font-size:12px;line-height:19.5px;color:#555}
.footer-col p{font-size:12px;line-height:20px;color:#555}
.contact-row{display:flex;gap:18px;align-items:center;font-size:12px;color:#555;margin-bottom:28px}
.map{width:242px;height:140px;background:linear-gradient(135deg,#eef0e6,#dfe6d3);border:1px solid var(--line)}
.bottom-rule{left:99px;top:2626px;width:1002px;height:1px;background:var(--line)}
.copyright{left:99px;top:2649px;font-size:11.5px;color:#555}
.socials{right:99px;top:2644px;display:flex;gap:8px}
.socials span{width:26px;height:26px;border-radius:50%;border:1.5px solid var(--orange)}
</style>
</head>
<body>

<header class="abs site-header">
  <div class="abs topbar">
    <span><i class="ico-ring"><svg width="16" height="12" viewBox="0 0 16 12"><rect x="0.5" y="0.5" width="15" height="11" rx="1.5" fill="none" stroke="#e05a2b" stroke-width="1.5"/><path d="M1 1l7 6 7-6" fill="none" stroke="#e05a2b" stroke-width="1.5"/></svg></i>hello@pebblebrookplots.com</span>
    <span><i class="ico-ring green"><svg width="16" height="16" viewBox="0 0 24 24"><path d="M6.6 10.8a15 15 0 006.6 6.6l2.2-2.2a1 1 0 011-.25 11.4 11.4 0 003.6.6 1 1 0 011 1V20a1 1 0 01-1 1A17 17 0 013 4a1 1 0 011-1h3.5a1 1 0 011 1c0 1.250.2 2.45.6 3.6a1 1 0 01-.25 1z" fill="#3a7d2c"/></svg></i>1 555 010 2040</span>
  </div>
  <nav class="abs main-nav">
    <span>Home</span><span>About Us</span><span>Products</span><span>Services</span><span>Gallery</span><span>Blog</span><span>Contact Us</span>
    <svg width="16" height="16" viewBox="0 0 16 16"><circle cx="6.5" cy="6.5" r="5" fill="none" stroke="#2b2b2b" stroke-width="2"/><path d="M10.5 10.5L15 15" stroke="#2b2b2b" stroke-width="2.2"/></svg>
  </nav>
</header>

<div class="abs logo-disc">
  <span class="logo-mark"></span>
  <span class="logo-name">PEBBLEBROOK<br>PLOTS</span>
</div>

<section class="abs hero" role="img" aria-label="Photo of a front lawn with flower beds and a house porch"></section>
<div class="abs hero-arrow" style="left:30px">&#8249;</div>
<div class="abs hero-arrow" style="right:22px">&#8250;</div>
<div class="abs hero-title">PEBBLEBROOK PLOTS</div>
<div class="abs hero-tag">We are a garden installation company</div>
<div class="abs btn-ghost">GET STARTED</div>

<form class="abs order-panel">
  <div class="order-head">ORDER NOW!</div>
  <div class="order-body">
    <div class="field-label" style="margin-top:4px">Size of Garden :</div>
    <div class="radios"><span><i class="dot on"></i>4' X 4'</span><span><i class="dot"></i>8' X 4'</span><span><i class="dot"></i>12' X 4'</span></div>
    <div class="field-label" style="margin-top:18px">Location :</div>
    <div class="select">- Select Location -<i>&#9662;</i></div>
    <div class="field-label">Installation Date :</div>
    <div class="select">- Select Date -<i><svg width="12" height="12" viewBox="0 0 12 12"><rect x="1" y="2" width="10" height="9" fill="none" stroke="#888"/><path d="M1 5h10" stroke="#888"/></svg></i></div>
    <div class="field-label">Payment :</div>
    <div class="cards"><span class="card">Amber</span><span class="card">Mosaic</span><span class="card">Vireo</span><span class="card">Meadow</span><span class="card">Plover</span></div>
    <div class="btn-green" style="width:114px;height:42px;margin:16px auto 0;font-size:14px">SUBMIT</div>
  </div>
</form>

<!-- how it works -->
<h2 class="abs section-title" style="top:580px">How it Works</h2>
<p class="abs intro" style="top:630px">At vero eos et accusamus et iusto odio dignissimos ducimus qui blanditiis praesentium voluptatum deleniti atque corrupti quos dolores et quas molestias excepturi sint occaecati cupiditate</p>

<div class="abs connector" style="left:328px"></div>
<div class="abs connector" style="left:694px"></div>
<svg class="abs" style="left:405px;top:788px" width="20" height="32" viewBox="0 0 20 32"><path d="M4 4l12 12L4 28" fill="none" stroke="#bbb" stroke-width="5"/></svg>
<svg class="abs" style="left:771px;top:788px" width="20" height="32" viewBox="0 0 20 32"><path d="M4 4l12 12L4 28" fill="none" stroke="#bbb" stroke-width="5"/></svg>

<div class="abs step" style="left:69px;top:719px">
  <div class="step-ring"><div class="step-core">
    <svg width="72" height="60" viewBox="0 0 72 60"><g fill="#e05a2b"><path d="M4 14l5-8 5 8v46H4z"/><path d="M22 14l5-8 5 8v46H22z"/><path d="M40 14l5-8 5 8v46H40z"/><path d="M58 14l5-8 5 8v46H58z"/><rect x="0" y="22" width="72" height="6"/><rect x="0" y="42" width="72" height="6"/></g></svg>
  </div></div>
  <h3>Step 1</h3>
  <p style="padding:0 48px">Select garden size. Either an 4' X 4', 8' X 4', or 12' X 4'.</p>
</div>
<div class="abs step" style="left:433px;top:719px">
  <div class="step-ring green"><div class="step-core">
    <svg width="70" height="72" viewBox="0 0 70 72"><path d="M35 4a19 19 0 0119 19c0 15-19 33-19 33S16 38 16 23A19 19 0 0135 4z" fill="#3a7d2c"/><circle cx="35" cy="23" r="7" fill="#fff"/><ellipse cx="35" cy="60" rx="30" ry="8" fill="none" stroke="#3a7d2c" stroke-width="4"/></svg>
  </div></div>
  <h3>Step 2</h3>
  <p style="padding:0 4px">Select a location. We would like to use an online map to look up a US address, then "drag and drop" one of the garden sizes from step 1 to the location the customer would like us to install the garden at their home.</p>
</div>
<div class="abs step" style="left:800px;top:719px">
  <div class="step-ring"><div class="step-core">
    <svg width="70" height="66" viewBox="0 0 70 66"><g fill="none" stroke="#e05a2b" stroke-width="5"><rect x="4" y="10" width="60" height="48" rx="4"/><path d="M4 24h60M18 3v13M50 3v13"/><circle cx="26" cy="46" r="12" fill="#fff"/><path d="M20 46l5 5 9-10"/></g></svg>
  </div></div>
  <h3>Step 3</h3>
  <p style="padding:0 6px">Pick an installation date and pay. Using an online calendar the customer will pick a date, and then pay for the installation via credit card.</p>
</div>

<!-- what we do -->
<section class="abs what"></section>
<h2 class="abs" style="left:99px;top:1138px">What We Do</h2>
<p class="abs" style="left:99px;top:1195px;width:460px">At vero eos et accusamus et iusto odio dignissimos ducimus qui blanditiis praesent ium voluptatum deleniti atque corrupti quo.</p>
<p class="abs" style="left:99px;top:1270px;width:460px">Dolores et quas molestias excepturi sint occaecati cupiditate non provident similiq ue sunt in culpa qui officia deserunt mollitia animi, id est laborum et dolorum fug t harum quidem rerum facilis est et expedita voluptas assumenda est, omnis dolorr epellend poribus autem quibusdam et aut officiis.</p>
<div class="abs btn-outline" style="left:96px;top:1393px;width:138px;height:34px">READ MORE &gt;&gt;</div>
<div class="abs video" role="img" aria-label="Video still of carrots growing in dark soil">
  <div class="abs play"><svg width="20" height="22" viewBox="0 0 20 22"><path d="M2 1l17 10L2 21z" fill="#fff"/></svg></div>
</div>

<!-- services -->
<section class="abs services"><h2 class="abs section-title" style="top:40px">Our Services</h2></section>
<article class="abs service-card" style="left:99px">
  <div class="service-img" role="img" aria-label="Photo of a stone garden path lined with flowers" style="background:linear-gradient(135deg,#c9a25a,#7fae4a 50%,#d84a5a)"></div>
  <h3>Garden Design</h3>
  <p>Nam libero tempore, cum soluta nobis est eligendi optio cumque nihil impedit quo minus id quod maxime placeat facere possim</p>
  <span class="btn-green">READ MORE &gt;&gt;</span>
</article>
<article class="abs service-card" style="left:445px">
  <div class="service-img" role="img" aria-label="Photo of a worker laying stone edging" style="background:linear-gradient(135deg,#9a948a,#6f6a62 50%,#3f5b8a)"></div>
  <h3>Garden Installation</h3>
  <p>Nam libero tempore, cum soluta nobis est eligendi optio cumque nihil impedit quo minus id quod maxime placeat facere possim</p>
  <span class="btn-green">READ MORE &gt;&gt;</span>
</article>
<article class="abs service-card" style="left:792px">
  <div class="service-img" role="img" aria-label="Photo of a hedge being trimmed" style="background:linear-gradient(135deg,#8a8a70,#5e9a32 50%,#3f7a22)"></div>
  <h3>Garden Maintenance</h3>
  <p>Nam libero tempore, cum soluta nobis est eligendi optio cumque nihil impedit quo minus id quod maxime placeat facere possim</p>
  <span class="btn-green">READ MORE &gt;&gt;</span>
</article>

<!-- gallery -->
<h2 class="abs section-title" style="top:2056px">Our Gallery</h2>
<div class="abs g-arrow" style="left:52px">&#8249;</div>
<div class="abs g-arrow" style="right:52px">&#8250;</div>
<div class="abs gallery-img" style="left:99px;background:linear-gradient(180deg,#9ec2e0,#8a6a50 45%,#5a9a32)" role="img" aria-label="Photo of a house with a green lawn"></div>
<div class="abs gallery-img" style="left:353px;background:linear-gradient(160deg,#8a7a6a,#5a4530)" role="img" aria-label="Photo of hands planting seedlings"></div>
<div class="abs gallery-img" style="left:608px;background:linear-gradient(180deg,#8ab4d8,#b8905a 55%,#6a8a4a)" role="img" aria-label="Photo of a modern house with a rock garden"></div>
<div class="abs gallery-img" style="left:862px;background:linear-gradient(180deg,#7a8a6a,#c85a6a 45%,#4f9a2e)" role="img" aria-label="Photo of a lawn bordered by flower beds"></div>

<!-- footer -->
<div class="abs footer-rule"></div>
<div class="abs footer-col" style="left:99px;top:2422px">
  <h4>Information</h4>
  <ul><li>Home</li><li>About Us</li><li>Products</li><li>Services</li><li>Gallery</li><li>Blog</li><li>Contact Us</li></ul>
</div>
<div class="abs footer-col" style="left:278px;top:2422px;width:260px">
  <h4>Newsletter Subscription</h4>
  <p>Register your Email Address to get information about us</p>
  <div style="margin-top:14px;padding:0 0 8px 14px;border-bottom:1px solid var(--line);font-size:11px;color:#999;width:256px">Email Address</div>
  <div class="btn-green" style="width:98px;height:32px;font-size:11px;margin-top:16px">SUBSCRIBE</div>
</div>
<div class="abs footer-col" style="left:593px;top:2422px">
  <h4>Contact Us</h4>
  <div class="contact-row"><svg width="12" height="16" viewBox="0 0 12 16"><path d="M6 0a6 6 0 016 6c0 4-6 10-6 10S0 10 0 6a6 6 0 016-6z" fill="#e05a2b"/><circle cx="6" cy="6" r="2.2" fill="#fff"/></svg>204 Willow Lane, Maple Ridge, BC</div>
  <div class="contact-row"><svg width="14" height="14" viewBox="0 0 24 24"><path d="M6.6 10.8a15 15 0 006.6 6.6l2.2-2.2a1 1 0 011-.25 11.4 11.4 0 003.6.6 1 1 0 011 1V20a1 1 0 01-1 1A17 17 0 013 4a1 1 0 011-1h3.5a1 1 0 011 1c0 1.25.2 2.45.6 3.6a1 1 0 01-.25 1z" fill="#e05a2b"/></svg>1 555 010 2040</div>
  <div class="contact-row"><svg width="14" height="11" viewBox="0 0 16 12"><rect width="16" height="12" rx="1.5" fill="#e05a2b"/><path d="M1 1l7 6 7-6" fill="none" stroke="#fff" stroke-width="1.4"/></svg>hello@pebblebrookplots.com</div>
</div>
<div class="abs footer-col" style="left:858px;top:2422px">
  <h4>Locations</h4>
  <div class="map" role="img" aria-label="Map of service locations with green markers"></div>
</div>
<div class="abs bottom-rule"></div>
<div class="abs copyright">Copyrights © 2017, Pebblebrook Plots. All rights reserved.</div>
<div class="abs socials"><span></span><span></span><span></span><span></span></div>

</body>
</html>
```